Business card for Luxury Portable Restroom Trailer company

We are a Luxury Portable Restroom Trailer Company Called FALCRIDGE HIRES. Based in Orange County California. We provide portable restroom trailers for events, such as, Weddings, Concerts, Charity events, Sporting events, Tournaments, Corporate events, ect. We rent and Sell the Luxury restrooms. Our colors are white, grey, and Orange. As you will see in the logo we uploaded.
There are 2 people in the company so the names and titles will change for the 3 people but card will remain the same. Here is the information for each Person: Dwight Penner CFO 555 318-0476
next Person: Leon Marchetti VP 555 318-0476
Next Person: Owen Marchetti CEO 555 318-0476
Information to include on the card: Luxury Restroom Trailers Rental and Sales. Weddings, Concerts, Charity, Sporting and Corp. Events.

```html
<!DOCTYPE html>
<html lang="en">
<head>
<meta charset="UTF-8">
<title>Falcridge Hires — Business Card</title>
<link href="https://fonts.googleapis.com/css2?family=Montserrat:wght@400;500;700;800&display=swap" rel="stylesheet">
<style>
  :root {
    --page: #2a2a2d;
    --card: #141414;
    --card-back: #101010;
    --orange: #f26a21;
    --white: #f2f2f2;
    --grey: #9a9a9a;
    --emboss: #1c1c1c;
  }
  * { margin: 0; padding: 0; box-sizing: border-box; }
  html, body { width: 1200px; height: 900px; overflow: hidden; }
  body {
    background: var(--page);
    font-family: "Montserrat", sans-serif;
    display: flex;
    flex-direction: column;
    align-items: center;
    justify-content: center;
    gap: 40px;
  }
  .card {
    width: 700px;
    height: 400px;
    border-radius: 18px;
    position: relative;
    overflow: hidden;
  }
  /* Back side */
  .card--back { background: var(--card-back); display: flex; align-items: center; justify-content: center; }
  .back-mark { display: flex; align-items: center; gap: 22px; }
  .back-mark__square { width: 46px; height: 46px; background: var(--emboss); }
  .back-mark__name {
    font-weight: 800;
    font-size: 58px;
    letter-spacing: 2px;
    color: var(--emboss);
  }
  /* Front side */
  .card--front { background: var(--card); }
  .accent-bar {
    position: absolute; top: 0; right: 0;
    width: 34px; height: 70px;
    background: var(--orange);
  }
  .person { position: absolute; top: 18px; right: 48px; text-align: right; }
  .person__name { color: var(--orange); font-weight: 700; font-size: 26px; }
  .person__title { color: var(--white); font-weight: 400; font-size: 14px; margin-top: 2px; }
  .mascot-panel {
    position: absolute; right: 0; top: 110px;
    width: 290px; height: 290px;
    border-radius: 60px 0 0 0;
    background: linear-gradient(150deg, #4a4a4a 0%, #262626 45%, #181818 100%);
  }
  .brand { position: absolute; left: 48px; top: 110px; width: 340px; }
  .brand__row { display: flex; align-items: center; gap: 10px; }
  .brand__square { width: 16px; height: 16px; background: var(--orange); }
  .brand__name { color: var(--orange); font-weight: 800; font-size: 26px; letter-spacing: 1px; }
  .brand__services {
    margin-top: 10px;
    color: var(--grey);
    font-size: 11.5px;
    font-weight: 500;
    line-height: 1.45;
  }
  .contact { position: absolute; left: 48px; bottom: 36px; color: var(--white); font-size: 14px; font-weight: 500; }
  .contact__address { line-height: 1.35; margin-bottom: 12px; }
  .contact__list { list-style: none; }
  .contact__item { display: flex; align-items: center; gap: 12px; line-height: 1.6; }
  .contact__icon { width: 14px; height: 14px; fill: var(--orange); flex: none; }
</style>
</head>
<body>

<section class="card card--back" aria-label="Card back">
  <div class="back-mark">
    <span class="back-mark__square"></span>
    <span class="back-mark__name">FALCRIDGE HIRES</span>
  </div>
</section>

<section class="card card--front" aria-label="Card front">
  <div class="accent-bar"></div>
  <div class="person">
    <p class="person__name">Owen Marchetti</p>
    <p class="person__title">CEO</p>
  </div>

  <div class="mascot-panel" role="img" aria-label="Large glossy grey brand emblem decoration"></div>

  <div class="brand">
    <div class="brand__row">
      <span class="brand__square"></span>
      <span class="brand__name">FALCRIDGE HIRES</span>
    </div>
    <p class="brand__services">Luxury Restroom Trailers Rental and Sales.<br>Weddings, Concerts, Charity, Sporting and Corp. Events.</p>
  </div>

  <div class="contact">
    <p class="contact__address">418 Harbor Crest Ave, #12<br>Costa Mesa, CA 92626</p>
    <ul class="contact__list">
      <li class="contact__item">
        <svg class="contact__icon" viewBox="0 0 16 16"><path d="M2 5c0-2 2-3 6-3s6 1 6 3v2h-3V5.5H5V7H2z M4 8h8l2 6H2z"/></svg>
        555 318-0476
      </li>
      <li class="contact__item">
        <svg class="contact__icon" viewBox="0 0 16 16"><path d="M4 1h8v14H4z M5.5 2.5v10h5v-10z"/></svg>
        555 318-0476
      </li>
      <li class="contact__item">
        <svg class="contact__icon" viewBox="0 0 16 16"><path d="M1 3h14v10H1z M2 4l6 5 6-5"/></svg>
        info@falcridgehires.com
      </li>
      <li class="contact__item">
        <svg class="contact__icon" viewBox="0 0 16 16"><circle cx="8" cy="8" r="7"/></svg>
        www.falcridgehires.com
      </li>
    </ul>
  </div>
</section>

</body>
</html>
```